A Label for an ECO Friendly Spirit Company

Design a label which can be used for vodka and gin (London Dry Gin). It should be Square type Like the Shape File you see in the uploads. KIRO means Kind Inventive Rare and Original. We want a cool and slim label that calls for eco-friendly. We want to use it for our premium
Vodka and our London Dry Gin. Please use the logo and design it in Square Type.

40%vol, 700ml

Target Market(s)

spirits and events

Industry/Entity Type

SPIRITS

Colors
00AB8E
00BBA5
67D7C9
C6EFE9
E9F9F6
59FF00
82FF00
B8FF75
E3FFCB
F4FFEA

Requirements
Must have
• Logo from KIRO, Squaee Shape

```html
<!DOCTYPE html>
<html lang="en">
<head>
<meta charset="utf-8">
<title>KIRO Spirits – Square Labels</title>
<link rel="stylesheet" href="https://fonts.googleapis.com/css2?family=Sancreek&family=Roboto+Condensed:wght@700&display=swap">
<style>
  :root {
    --canvas: #ffffff;
    --band-light: #8dc63f;
    --band-dark: #2f6b22;
    --field-core: #43b649;
    --field-mid: #17702e;
    --field-edge: #06301a;
    --rule: #8dc63f;
    --brand-teal: #00a88c;
    --tag-green: #7ac143;
    --tag-teal: #00ab8e;
    --white: #ffffff;
  }
  html, body {
    margin: 0;
    padding: 0;
    width: 1200px;
    height: 1000px;
    overflow: hidden;
    background: var(--canvas);
  }
  .label-sheet { display: block; width: 1200px; height: 1000px; }
  .brand-name {
    font-family: "Roboto Condensed", sans-serif;
    font-weight: 700;
    font-size: 32px;
    letter-spacing: 2px;
    fill: var(--brand-teal);
  }
  .product-title {
    font-family: "Sancreek", serif;
    fill: var(--white);
  }
  .tagline {
    font-family: "Roboto Condensed", sans-serif;
    font-weight: 700;
    font-size: 12.5px;
    letter-spacing: 1.6px;
  }
  .tagline-primary { fill: var(--tag-green); }
  .tagline-secondary { fill: var(--tag-teal); }
  .spec {
    font-family: "Roboto Condensed", sans-serif;
    font-weight: 700;
    font-size: 11px;
    letter-spacing: 0.8px;
    fill: var(--white);
  }
</style>
</head>
<body>
<svg class="label-sheet" viewBox="0 0 1200 1000" xmlns="http://www.w3.org/2000/svg">
  <defs>
    <linearGradient id="band-gradient" x1="0" y1="0" x2="1" y2="1">
      <stop offset="0" stop-color="var(--band-dark)"/>
      <stop offset="0.5" stop-color="#4f9a2f"/>
      <stop offset="1" stop-color="var(--band-light)"/>
    </linearGradient>
    <radialGradient id="field-gradient" cx="0.5" cy="0.5" r="0.5">
      <stop offset="0" stop-color="var(--field-core)"/>
      <stop offset="0.55" stop-color="var(--field-mid)"/>
      <stop offset="1" stop-color="var(--field-edge)"/>
    </radialGradient>
    <filter id="title-shadow" x="-10%" y="-10%" width="120%" height="130%">
      <feDropShadow dx="2" dy="3" stdDeviation="1.5" flood-color="#02200f" flood-opacity="0.7"/>
    </filter>
  </defs>

  <g class="label label-vodka" transform="translate(320 488)">
    <polygon class="label-band" points="0,-252 252,0 0,252 -252,0" fill="url(#band-gradient)"/>
    <polygon class="label-field" points="0,-225 225,0 0,225 -225,0" fill="url(#field-gradient)"/>
    <polygon class="label-rule" points="0,-236 236,0 0,236 -236,0" fill="none" stroke="var(--rule)" stroke-width="1.2"/>
    <text class="brand-name" x="0" y="-58" text-anchor="middle">KIRO</text>
    <text class="product-title" x="-2" y="54" text-anchor="middle" font-size="96" textLength="300" lengthAdjust="spacingAndGlyphs" filter="url(#title-shadow)">VODKA</text>
    <text class="tagline tagline-primary" x="0" y="106" text-anchor="middle">KIND ORIGINAL</text>
    <text class="tagline tagline-secondary" x="0" y="124" text-anchor="middle">PREMIUM</text>
    <text class="spec" x="0" y="159" text-anchor="middle">40%</text>
    <text class="spec" x="0" y="175" text-anchor="middle">Vol. 700ml</text>
  </g>

  <g class="label label-gin" transform="translate(880 488)">
    <polygon class="label-band" points="0,-252 252,0 0,252 -252,0" fill="url(#band-gradient)"/>
    <polygon class="label-field" points="0,-225 225,0 0,225 -225,0" fill="url(#field-gradient)"/>
    <polygon class="label-rule" points="0,-236 236,0 0,236 -236,0" fill="none" stroke="var(--rule)" stroke-width="1.2"/>
    <text class="brand-name" x="0" y="-80" text-anchor="middle">KIRO</text>
    <text class="product-title" x="3" y="0" text-anchor="middle" font-size="80" textLength="262" lengthAdjust="spacingAndGlyphs" filter="url(#title-shadow)">LONDON</text>
    <text class="product-title" x="5" y="82" text-anchor="middle" font-size="80" textLength="240" lengthAdjust="spacingAndGlyphs" filter="url(#title-shadow)">DRY GIN</text>
    <text class="tagline tagline-primary" x="0" y="116" text-anchor="middle">KIND ORIGINAL</text>
    <text class="tagline tagline-secondary" x="0" y="134" text-anchor="middle">PREMIUM</text>
    <text class="spec" x="0" y="159" text-anchor="middle">40%</text>
    <text class="spec" x="0" y="175" text-anchor="middle">Vol. 700ml</text>
  </g>
</svg>
</body>
</html>
```